CLEARPATH COUNSEL

I'm virtually ready to launch my site, but I have a number of edits and modifications that need to be implemented. More importantly, I'm always looking to improve my site, particularly now that I am making my proverbial "FIRST IMPRESSION." Thus, I'm willing to see if there is someone who can add creativity and perhaps improve what I already have, particularly on the All Important Front Page.

```html
<!DOCTYPE html>
<html lang="en">
<head>
<meta charset="utf-8">
<title>Clearpath Counsel</title>
<link href="https://fonts.googleapis.com/css2?family=Ubuntu:wght@400;500;700&family=Open+Sans:wght@400;600;700&display=swap" rel="stylesheet">
<style>
:root{
  --navy:#13295b;
  --navy-dark:#0d1c3f;
  --red:#a50d12;
  --ink:#222;
  --muted:#777;
  --light:#f2f2f2;
  --footer:#101b30;
  --white:#fff;
}
*{box-sizing:border-box;margin:0;padding:0}
html,body{width:1200px;height:4967px;overflow:hidden}
body{position:relative;font-family:"Open Sans",sans-serif;color:var(--ink);background:var(--white)}
.abs{position:absolute}
h1,h2,h3,h4{font-family:"Ubuntu",sans-serif;font-weight:500}
.label{font-size:11px;color:var(--red);text-transform:uppercase;letter-spacing:.3px;display:flex;align-items:center;gap:12px}
.label .rule{display:block;width:46px;height:2px;background:var(--red)}
.heading{color:var(--navy);font-size:46px;line-height:1.38}
.btn-red{background:var(--red);color:#fff;font-size:13px;font-weight:700;display:flex;align-items:center;justify-content:center;border-radius:4px}
p.body{font-size:12.5px;color:var(--muted);line-height:24px}
.photo{background:linear-gradient(135deg,#4a5162,#23293a)}

/* header */
.top-bar{left:0;top:0;width:1200px;height:105px;background:#fff}
.brand{left:96px;top:16px;display:flex;align-items:center;gap:8px;font-family:"Ubuntu",sans-serif;font-weight:700;font-size:13px;color:var(--navy)}
.brand .dot{width:48px;height:48px;border-radius:50%;background:var(--navy)}
.info{display:flex;gap:14px;align-items:center;font-size:11px;color:#333}
.info b{display:block;font-weight:600;font-size:10px;text-transform:uppercase}
.quote-btn{left:945px;top:20px;width:168px;height:48px;background:var(--navy);color:#fff;font-size:12px;font-weight:700;display:flex;align-items:center;justify-content:center;border-radius:3px}
.nav{left:85px;top:80px;width:1030px;height:62px;background:#fff;display:flex;align-items:center;padding:0 36px;font-size:13.5px;color:#444;box-shadow:0 3px 8px rgba(0,0,0,.12);z-index:2}
.nav span{margin-right:48px}
.social{margin-left:auto;display:flex;gap:10px}
.social i{width:36px;height:36px;border-radius:3px;display:block}

.hero{left:0;top:105px;width:1200px;height:688px;background:linear-gradient(120deg,#3d4250,#22262f 60%,#2d3240)}
.hero .veil{position:absolute;inset:0;background:rgba(15,18,28,.45)}
.welcome{left:510px;top:330px;width:162px;height:36px;background:var(--navy);color:#fff;font-size:12px;display:flex;align-items:center;justify-content:center;border-radius:3px}
.hero-title{left:0;top:378px;width:1200px;text-align:center;color:#fff;font-size:62px;line-height:74px;font-weight:500}
.hero-btn{left:508px;top:548px;width:168px;height:48px;border:1.5px solid #fff;color:#fff;font-size:12px;font-weight:700;display:flex;align-items:center;justify-content:center;border-radius:3px}
.arrow-box{width:60px;height:60px;background:#fff;border-radius:3px;display:flex;align-items:center;justify-content:center}

/* services */
.services-bg{left:0;top:1460px;width:1200px;height:820px;background:var(--light)}
.card{width:321px;height:313px;border-radius:6px;overflow:hidden}
.card .shade{position:absolute;inset:0;background:linear-gradient(180deg,rgba(19,41,91,.25),rgba(13,28,63,.8))}
.card .ico{position:absolute;left:40px;top:45px;width:66px;height:66px;background:#fff;border-radius:8px;display:flex;align-items:center;justify-content:center}
.card h3{position:absolute;left:34px;top:148px;color:#fff;font-size:23px}
.card p{position:absolute;left:34px;top:212px;color:#eee;font-size:12.5px}
.card .more{position:absolute;left:34px;top:252px;color:#fff;font-size:15px;font-weight:700}
.card .line{position:absolute;left:34px;top:280px;width:250px;height:3px;background:var(--red)}

.cta{left:94px;top:2178px;width:1017px;height:208px;border-radius:6px;background:linear-gradient(90deg,#1e2c55,#15244d 60%,#0d1c3f)}
.cta h3{position:absolute;left:56px;top:95px;color:#fff;font-size:24px}
.cta .outline{position:absolute;left:589px;top:84px;width:165px;height:52px;border:1.5px solid #fff;color:#fff;font-size:14px;display:flex;align-items:center;justify-content:center}
.cta .phone{position:absolute;left:760px;top:84px;width:207px;height:52px;background:#fff;color:#222;font-size:15px;display:flex;align-items:center;justify-content:center;gap:10px}

/* why */
.why-item h4{color:var(--navy);font-size:20px}
.why-item p{font-size:12.5px;color:var(--muted);line-height:18px;margin-top:4px}
.ring{width:78px;height:78px;border-radius:50%;background:#fff;box-shadow:0 2px 12px rgba(0,0,0,.1);display:flex;align-items:center;justify-content:center}
.why-portrait{left:433px;top:2610px;width:330px;height:330px;border-radius:50%;background:linear-gradient(135deg,#33497f,#15244d)}

/* testimonials */
.tcard{height:208px;background:#fff;border-radius:6px;box-shadow:0 2px 12px rgba(0,0,0,.08);padding:28px 24px}
.tcard p{font-size:12.5px;color:var(--muted);line-height:24px}
.tcard .who{display:flex;align-items:center;gap:12px;margin-top:14px;font-size:12px;font-weight:700}
.tcard .av{width:50px;height:50px;border-radius:50%;background:linear-gradient(135deg,#b9a08a,#5f6f85)}
.tcard .q{margin-left:auto;font-family:Georgia,serif;font-size:46px;color:var(--navy);line-height:20px}

/* contact */
.field{height:48px;border:1px solid #ccc;border-radius:3px;font-size:12px;color:#999;padding:0 16px;display:flex;align-items:center}

/* footer */
.footer{left:0;top:4400px;width:1200px;height:500px;background:var(--footer)}
.strip{left:85px;top:4400px;width:1030px;height:158px;background:#fff;display:flex}
.strip div{flex:1;display:flex;flex-direction:column;align-items:center;justify-content:center;gap:18px;font-size:15px;font-weight:600;color:#333;border-right:1px solid #ddd;margin:20px 0}
.strip div:last-child{border:none}
.fcol{color:#cfd4de;font-size:12.5px;line-height:22px}
.fcol h4{color:#fff;font-size:17px;margin-bottom:24px}
.links{display:grid;grid-template-columns:170px 150px;row-gap:11px;font-size:12.5px;color:#cfd4de}
.bottom{left:0;top:4900px;width:1200px;height:67px;background:#dde3ed;display:flex;align-items:center;padding:0 86px;font-size:11px;font-weight:700;color:var(--navy)}
.bottom .soc{margin-left:auto;display:flex;gap:26px}
.bottom .soc i{width:10px;height:10px;border-radius:50%;background:var(--navy);display:block}
</style>
</head>
<body>

<!-- header -->
<div class="abs top-bar"></div>
<div class="abs brand"><span class="dot"></span>Clearpath Counsel</div>
<div class="abs info" style="left:428px;top:22px">
  <svg width="30" height="30" viewBox="0 0 24 24" fill="none" stroke="#13295b" stroke-width="1.8"><path d="M12 22s7-7 7-12a7 7 0 0 0-14 0c0 5 7 12 7 12z"/><circle cx="12" cy="10" r="2.5"/></svg>
  <div><b>Location</b>77 Elm St, City</div>
</div>
<div class="abs" style="left:652px;top:20px;width:1px;height:48px;background:#ddd"></div>
<div class="abs info" style="left:678px;top:22px">
  <svg width="34" height="34" viewBox="0 0 24 24" fill="none" stroke="#13295b" stroke-width="1.8"><circle cx="12" cy="12" r="9"/><path d="M8 12h8m-3-3 3 3-3 3"/></svg>
  <div><b>Office Hours</b>9.00 to 7.00 &nbsp;[Sun: Closed]</div>
</div>
<div class="abs quote-btn">REQUEST A QUOTE</div>
<nav class="abs nav">
  <span>Home</span><span>About Us</span><span>Services</span><span style="margin-left:12px">Solutions</span><span>Team</span><span>Gallery</span><span>Contact Us</span>
  <div class="social"><i style="background:#3b5a9a"></i><i style="background:#d3202a"></i><i style="background:#3aa2e4"></i></div>
</nav>

<section class="abs hero" role="img" aria-label="Lawyers in a meeting around a conference table"><div class="veil"></div></section>
<div class="abs welcome">WELCOME</div>
<h1 class="abs hero-title">Turning Challenges into<br>Legal Triumphs</h1>
<div class="abs hero-btn">ABOUT COMPANY</div>
<div class="abs arrow-box" style="left:44px;top:490px"><svg width="22" height="22" viewBox="0 0 24 24" fill="none" stroke="#13295b" stroke-width="2.4"><path d="M20 12H5m6-6-6 6 6 6"/></svg></div>
<div class="abs arrow-box" style="left:1095px;top:490px"><svg width="22" height="22" viewBox="0 0 24 24" fill="none" stroke="#13295b" stroke-width="2.4"><path d="M4 12h15m-6-6 6 6-6 6"/></svg></div>

<!-- about -->
<div class="abs" style="left:96px;top:920px;width:445px;height:436px;border-radius:50%;background:var(--navy)"></div>
<div class="abs photo" role="img" aria-label="Smiling lawyer seated at a desk" style="left:118px;top:930px;width:420px;height:426px;border-radius:50%;background:linear-gradient(135deg,#8d939c,#4d5560)"></div>
<div class="abs" style="left:436px;top:1248px;width:100px;height:100px;border-radius:50%;background:#fff;box-shadow:0 3px 10px rgba(0,0,0,.15);display:flex;align-items:center;justify-content:center"><span style="width:56px;height:56px;border-radius:50%;background:var(--navy);display:block"></span></div>
<div class="abs label" style="left:612px;top:940px">About Us<span class="rule"></span></div>
<h2 class="abs heading" style="left:608px;top:964px">Strategic Solutions,<br>Legal Excellence</h2>
<p class="abs body" style="left:612px;top:1106px;width:440px">Lorem ipsum dolor sit amet, consectetur adipiscing elit, sed do eiusmod tempor incididunt ut labore et dolore magna aliqua. Ut enim ad min im veniam, quis nostrud exercitation ullamco laboris nisi ut aliquip ex ea commodo consequat. Duis aute irure dolor in reprehenderit in voluptate velit esse cillum dolore eu fugiat nulla pariatur. Excepteur sint occaecat cupidatat non proident, sunt in culpa qui officia deserunt mollit anim id est laborum.</p>
<div class="abs btn-red" style="left:612px;top:1294px;width:168px;height:44px">Contact Us</div>

<!-- services -->
<div class="abs services-bg"></div>
<div class="abs label" style="left:90px;top:1543px">About Us<span class="rule"></span></div>
<h2 class="abs heading" style="left:88px;top:1570px">Services We Provide</h2>
<div class="abs arrow-box" style="left:998px;top:1560px;width:46px;height:62px;box-shadow:0 2px 6px rgba(0,0,0,.1)"><svg width="16" height="16" viewBox="0 0 24 24" fill="none" stroke="#111" stroke-width="3"><path d="m15 5-7 7 7 7"/></svg></div>
<div class="abs arrow-box" style="left:1050px;top:1560px;width:46px;height:62px;box-shadow:0 2px 6px rgba(0,0,0,.1)"><svg width="16" height="16" viewBox="0 0 24 24" fill="none" stroke="#111" stroke-width="3"><path d="m9 5 7 7-7 7"/></svg></div>

<div class="abs card" style="left:92px;top:1682px" role="img" aria-label="Scales of justice and gavel montage">
  <div class="photo" style="position:absolute;inset:0;background:linear-gradient(135deg,#5b6a87,#24345a)"></div><div class="shade"></div>
  <div class="ico"><svg width="36" height="36" viewBox="0 0 24 24" stroke="#13295b" stroke-width="2" stroke-linecap="round"><path d="M12 3v3M12 18v3M3 12h3M18 12h3M5.6 5.6l2.1 2.1M16.3 16.3l2.1 2.1M5.6 18.4l2.1-2.1M16.3 7.7l2.1-2.1"/></svg></div>
  <h3>Consultation</h3><p>Lorem ipsum dolor sit amet, consectetur</p><div class="more">Read More</div><div class="line"></div>
</div>
<div class="abs card" style="left:440px;top:1682px" role="img" aria-label="Judge's gavel on a desk">
  <div class="photo" style="position:absolute;inset:0;background:linear-gradient(135deg,#4a3c34,#1c1d24)"></div><div class="shade" style="background:linear-gradient(180deg,rgba(0,0,0,.1),rgba(10,12,20,.7))"></div>
  <div class="ico"><svg width="36" height="36" viewBox="0 0 24 24" fill="none" stroke="#13295b" stroke-width="2"><circle cx="12" cy="12" r="9"/><path d="m9 9-3 3 3 3m6-6 3 3-3 3"/></svg></div>
  <h3>Litigation</h3><p>Lorem ipsum dolor sit amet, consectetur</p><div class="more">Read More</div><div class="line"></div>
</div>
<div class="abs card" style="left:787px;top:1682px" role="img" aria-label="Team of professionals in a meeting">
  <div class="photo" style="position:absolute;inset:0;background:linear-gradient(135deg,#7a5e4b,#2a3355)"></div><div class="shade"></div>
  <div class="ico"><svg width="36" height="36" viewBox="0 0 24 24" fill="none" stroke="#13295b" stroke-width="2"><path d="M4 6h16M4 9h16"/><circle cx="8" cy="15" r="3"/><circle cx="16" cy="15" r="3"/></svg></div>
  <h3>Collection Claims</h3><p>Lorem ipsum dolor sit amet, consectetur</p><div class="more">Read More</div><div class="line"></div>
</div>
<div class="abs btn-red" style="left:511px;top:2070px;width:168px;height:46px">Contact Us</div>

<div class="abs cta" role="img" aria-label="Banner of professionals at work under a navy tint">
  <h3>Delivering Results with Solid Dependability</h3>
  <div class="outline">Get A Quote</div>
  <div class="phone"><svg width="20" height="20" viewBox="0 0 24 24" fill="#111"><path d="M6.6 10.8a15 15 0 0 0 6.6 6.6l2.2-2.2c.3-.3.7-.4 1-.2 1.1.4 2.3.6 3.6.6.6 0 1 .4 1 1V20c0 .6-.4 1-1 1A17 17 0 0 1 3 4c0-.6.4-1 1-1h3.5c.6 0 1 .4 1 1 0 1.3.2 2.5.6 3.6.1.3 0 .7-.2 1z"/></svg>0800 - 555 - 0142</div>
</div>

<!-- why choose us -->
<div class="abs label" style="left:514px;top:2443px"><span class="rule"></span>Why Choose Us<span class="rule"></span></div>
<h2 class="abs heading" style="left:0;top:2462px;width:1222px;text-align:center">Why Choose Us</h2>
<div class="abs why-portrait" role="img" aria-label="Smiling lawyer in a grey suit with arms crossed"></div>

<div class="abs why-item" style="left:148px;top:2618px"><h4>Client Centric</h4><p>&nbsp;Lorem ipsum dolor sit amet,<br>&nbsp;consectetur adipiscing elit</p></div>
<div class="abs ring" style="left:356px;top:2613px"><svg width="34" height="34" viewBox="0 0 24 24" fill="none" stroke="#a50d12" stroke-width="2"><circle cx="12" cy="4" r="2"/><path d="M5 9h14M12 9v5l-4 7m4-7 4 7"/></svg></div>
<div class="abs why-item" style="left:116px;top:2743px"><h4>Free Consultation</h4><p>&nbsp;Lorem ipsum dolor sit amet,<br>&nbsp;consectetur adipiscing elit</p></div>
<div class="abs ring" style="left:320px;top:2738px"><svg width="34" height="34" viewBox="0 0 24 24" stroke="#a50d12" stroke-width="2" stroke-linecap="round"><path d="M12 3v3M12 18v3M3 12h3M18 12h3M5.6 5.6l2.1 2.1M16.3 16.3l2.1 2.1M5.6 18.4l2.1-2.1M16.3 7.7l2.1-2.1"/></svg></div>
<div class="abs why-item" style="left:132px;top:2868px"><h4>Minimize Exposure</h4><p>&nbsp;Lorem ipsum dolor sit amet,<br>&nbsp;consectetur adipiscing elit</p></div>
<div class="abs ring" style="left:352px;top:2863px"><svg width="34" height="34" viewBox="0 0 24 24" fill="none" stroke="#a50d12" stroke-width="2"><path d="M4 14a8 8 0 0 1 16 0v6H4zM4 14h16M9 17h6"/></svg></div>

<div class="abs ring" style="left:762px;top:2613px"><svg width="34" height="34" viewBox="0 0 24 24" fill="none" stroke="#a50d12" stroke-width="2"><circle cx="12" cy="12" r="9"/><circle cx="12" cy="12" r="5"/><circle cx="12" cy="12" r="1.5"/></svg></div>
<div class="abs why-item" style="left:890px;top:2618px"><h4>Attorney Letters</h4><p>&nbsp;Lorem ipsum dolor sit amet,<br>&nbsp;consectetur adipiscing elit</p></div>
<div class="abs ring" style="left:796px;top:2738px"><svg width="34" height="34" viewBox="0 0 24 24" fill="none" stroke="#a50d12" stroke-width="2"><path d="M4 14a8 8 0 0 1 16 0v6H4zM4 14h16M9 17h6"/></svg></div>
<div class="abs why-item" style="left:898px;top:2743px"><h4>Affordable</h4><p>&nbsp;Lorem ipsum dolor sit amet,<br>&nbsp;consectetur adipiscing elit</p></div>
<div class="abs ring" style="left:762px;top:2863px"><svg width="34" height="34" viewBox="0 0 24 24" fill="none" stroke="#a50d12" stroke-width="2"><rect x="3" y="3" width="5" height="5"/><rect x="16" y="3" width="5" height="5"/><rect x="3" y="16" width="5" height="5"/><rect x="16" y="16" width="5" height="5"/><path d="M8 5.5h8M8 18.5h8M18.5 8v8"/></svg></div>
<div class="abs why-item" style="left:875px;top:2868px"><h4>Legal Experts</h4><p>&nbsp;Lorem ipsum dolor sit amet,<br>&nbsp;consectetur adipiscing elit</p></div>

<!-- testimonials -->
<div class="abs" style="left:338px;top:3058px;width:862px;height:533px;background:var(--light)"></div>
<div class="abs photo" role="img" aria-label="Blurred crowd of business people" style="left:0;top:3058px;width:338px;height:533px;background:linear-gradient(160deg,#2c3550,#161d30)"></div>
<div class="abs label" style="left:574px;top:3118px"><span class="rule"></span>Testimonials<span class="rule"></span></div>
<h2 class="abs heading" style="left:406px;top:3142px">What Clients are Saying</h2>
<div class="abs tcard" style="left:135px;top:3258px;width:348px"><p>Lorem ipsum dolor sit amet, consectetur adipis por incididunt ut labore et dolore magna aliqu uis nostrud exercitation ullamco laboris nisi consequat. Duis aute irure dolor in reprehend</p><div class="who"><span class="av"></span>Mara Ellison<span class="q">&#8221;</span></div></div>
<div class="abs tcard" style="left:500px;top:3258px;width:343px;border-bottom:3px solid var(--navy)"><p>Lorem ipsum dolor sit amet, consectetur adipis por incididunt ut labore et dolore magna aliqu uis nostrud exercitation ullamco laboris nisi consequat. Duis aute irure dolor in reprehend</p><div class="who"><span class="av"></span>Mara Ellison<span class="q">&#8221;</span></div></div>
<div class="abs tcard" style="left:870px;top:3258px;width:360px;border-radius:6px 0 0 6px"><p>Lorem ipsum dolor sit amet, consectetur adipis por incididunt ut labore et dolore magna aliqu uis nostrud exercitation ullamco laboris nisi consequat. Duis aute irure dolor in reprehend</p><div class="who"><span class="av"></span>Mara Ellison<span class="q" style="margin-right:30px">&#8221;</span></div></div>
<div class="abs" style="left:630px;top:3507px;display:flex;gap:20px;align-items:center">
  <span style="width:16px;height:16px;border-radius:50%;border:2px solid #1a8fb0;display:flex;align-items:center;justify-content:center"><i style="width:6px;height:6px;border-radius:50%;background:#1a8fb0"></i></span>
  <i style="width:7px;height:7px;border-radius:50%;background:#999"></i><i style="width:7px;height:7px;border-radius:50%;background:#999"></i><i style="width:7px;height:7px;border-radius:50%;background:#999"></i>
</div>

<!-- contact -->
<div class="abs label" style="left:532px;top:3713px"><span class="rule"></span>Contact Us<span class="rule"></span></div>
<h2 class="abs heading" style="left:0;top:3736px;width:1260px;text-align:center">Get in touch with us</h2>
<div class="abs" style="left:90px;top:3845px;width:1020px;height:415px;background:#fff;box-shadow:0 2px 14px rgba(0,0,0,.1)"></div>
<div class="abs photo" role="img" aria-label="Two colleagues reviewing a tablet together" style="left:90px;top:3845px;width:420px;height:415px;background:linear-gradient(135deg,#c9ccd2,#6b6f7a)"></div>
<div class="abs" style="left:286px;top:4180px;width:198px;height:50px;background:#fff;display:flex;align-items:center;justify-content:center;gap:10px;font-size:16px">
  <svg width="18" height="18" viewBox="0 0 24 24" fill="#111"><path d="M6.6 10.8a15 15 0 0 0 6.6 6.6l2.2-2.2c.3-.3.7-.4 1-.2 1.1.4 2.3.6 3.6.6.6 0 1 .4 1 1V20c0 .6-.4 1-1 1A17 17 0 0 1 3 4c0-.6.4-1 1-1h3.5c.6 0 1 .4 1 1 0 1.3.2 2.5.6 3.6.1.3 0 .7-.2 1z"/></svg>1800-555-019</div>
<h3 class="abs" style="left:553px;top:3893px;font-size:22px;color:#333">Get a free consultation</h3>
<p class="abs" style="left:553px;top:3932px;width:500px;font-size:12.5px;color:var(--muted);line-height:22px">Get a free consultation from our experts, Our customer support team help you 24/7. Don't hesitate.</p>
<div class="abs field" style="left:554px;top:4010px;width:500px">Your Name</div>
<div class="abs field" style="left:554px;top:4080px;width:236px">Your Email</div>
<div class="abs field" style="left:816px;top:4080px;width:238px">Message</div>
<div class="abs btn-red" style="left:554px;top:4150px;width:500px;height:46px;font-size:11px;gap:8px">GET IN TOUCH <svg width="14" height="14" viewBox="0 0 24 24" fill="none" stroke="#fff" stroke-width="2.5"><path d="M4 12h15m-6-6 6 6-6 6"/></svg></div>

<!-- footer -->
<div class="abs" style="left:115px;top:4372px;width:980px;height:30px;background:#dfe7f2;clip-path:polygon(2% 0,100% 90%,100% 100%,0 100%)"></div>
<div class="abs footer"></div>
<div class="abs strip">
  <div><svg width="44" height="40" viewBox="0 0 24 24" fill="none" stroke="#3f87d6" stroke-width="1.4"><path d="M12 14s5-4.5 5-8.5a5 5 0 0 0-10 0C7 9.5 12 14 12 14z"/><circle cx="12" cy="5.5" r="1.8"/><path d="M3 21l3-6h12l3 6z"/></svg>Come to Our Location</div>
  <div><svg width="44" height="40" viewBox="0 0 24 24" fill="none" stroke="#3fae8c" stroke-width="1.4"><rect x="3" y="7" width="18" height="13"/><path d="m3 7 9 7 9-7M8 4h8"/></svg>Send Us an Email</div>
  <div><svg width="44" height="40" viewBox="0 0 24 24" fill="none" stroke="#3f87d6" stroke-width="1.4"><rect x="7" y="2" width="10" height="20" rx="2"/><path d="M11 18h2M19 9a4 4 0 0 1 0 6"/></svg>Give Us a Call</div>
</div>
<div class="abs" style="left:100px;top:4612px;display:flex;align-items:center;gap:10px;font-family:Ubuntu,sans-serif;font-weight:700;font-size:15px;color:#fff"><span style="width:64px;height:64px;border-radius:50%;background:var(--navy);display:block"></span>Clearpath Counsel</div>
<p class="abs fcol" style="left:85px;top:4692px;width:320px;line-height:21px">Lorem ipsum dolor sit amet, consectetur adipi por incididunt ut labore et dolore magna aliqu uis nostrud exercitation ullamco laboris nisi u a consequat. Duis aute irure dolor in reprehend</p>
<div class="abs fcol" style="left:438px;top:4614px"><h4>Visit Our Place</h4>18 Harbor Lane<br>Suite 4, 10001, USA<div style="margin-top:14px;font-size:11px;font-weight:700;color:#fff">FIND US ON MAP</div>
  <div style="margin-top:26px;width:308px;height:44px;border:1px solid #5a6479;display:flex;align-items:center;font-size:11px"><span style="flex:1;padding-left:12px">Enter Your Email...</span><span style="border-left:1px solid #5a6479;height:100%;display:flex;align-items:center;padding:0 12px;color:var(--red);font-weight:700">SUBSCRIBE</span></div>
</div>
<div class="abs fcol" style="left:790px;top:4614px"><h4>Useful Links</h4>
  <div class="links"><span>About Us</span><span>Testimonials</span><span>Practice areas</span><span>FAQs</span><span>Why Choose Us</span><span>Cookies</span><span>How it works</span><span>Contact Us</span><span>News &amp; Updates</span><span>Privacy Policy</span></div>
</div>
<div class="abs bottom">CLEARPATH COUNSEL<div class="soc"><i></i><i></i><i></i><i></i></div></div>
<div class="abs" style="left:1140px;top:4902px;width:48px;height:48px;background:var(--red);border-radius:4px;display:flex;align-items:center;justify-content:center"><svg width="20" height="20" viewBox="0 0 24 24" fill="none" stroke="#fff" stroke-width="3"><path d="m5 15 7-7 7 7"/></svg></div>

</body>
</html>
```